Corvane Business Cards

Front of business card will have logo, name, address, & telephone number. Back of card will have a list of services provided - Roads, Substation Pads, Temporary Pads, Site Pads, Land Leveling, Powerline Row Cleaning, Land Clearing, Gates, Fencing, Construction Entrances, Excavation, Trenching, Underground Utilities, Directional Boring, Pile Driving. We are a construction company that uses heavy equipment like bulldozers, motor graders/blades, dump trucks, backhoes, hydro axes, & skid loaders. We build roads, pads, & install electric utility lines & waterlines underground. This logo is new. The word "Construction" can be smaller as uploaded 2 example edited logos. We will be using this card design for many employees.
Target Market(s)
Industrial Electric Powerline, Wind Turbine, Solar Panel, & Water Utility companies.
Contact Information for Business Card
Name/Position - Dwayne Halster - Owner
Address: 4875 FM 309
Dunmore, TX 79412
Phone number - (325) 482-5096

```html
<!DOCTYPE html>
<html lang="en">
<head>
<meta charset="utf-8">
<title>Corvane Construction – Business Cards</title>
<link rel="stylesheet" href="https://fonts.googleapis.com/css2?family=Marcellus&family=Arimo:wght@400&family=Exo+2:wght@700&display=swap">
<style>
  :root {
    --maroon: #3a1219;
    --paper: #ffffff;
    --ink: #1e1e1e;
    --phone-grey: #3d3d3d;
    --backdrop: #d9d9d9;
    --card-shadow: rgba(0, 0, 0, 0.35);
  }
  * { margin: 0; padding: 0; box-sizing: border-box; }
  html, body {
    width: 1200px;
    height: 802px;
    overflow: hidden;
    background: var(--backdrop);
  }
  .canvas {
    position: relative;
    width: 1200px;
    height: 802px;
  }
  .card {
    position: absolute;
    top: 274px;
    width: 443px;
    height: 264px;
    box-shadow: 2px 3px 6px var(--card-shadow);
    overflow: hidden;
  }
  .card-front { left: 136px; background: var(--paper); }
  .card-back { left: 624px; background: var(--maroon); }

  /* Front */
  .name-band {
    position: absolute;
    left: 0;
    top: 36px;
    width: 192px;
    height: 82px;
    background: var(--maroon);
    color: var(--paper);
    padding: 24px 0 0 27px;
  }
  .person-name {
    font-family: "Marcellus", serif;
    font-size: 16px;
    letter-spacing: 1px;
    text-transform: uppercase;
    line-height: 1;
    white-space: nowrap;
  }
  .person-role {
    font-family: "Arimo", sans-serif;
    font-size: 12px;
    margin-top: 6px;
  }
  .brand-front {
    position: absolute;
    left: 218px;
    top: 48px;
    width: 210px;
    text-align: center;
    color: var(--maroon);
    font-family: "Marcellus", serif;
    font-size: 22px;
    line-height: 1.35;
    letter-spacing: 1px;
    text-transform: uppercase;
  }
  .brand-mark {
    display: block;
    width: 34px;
    height: 34px;
    margin: 0 auto 12px;
    border-radius: 50%;
    background: var(--maroon);
  }
  .address {
    position: absolute;
    left: 32px;
    top: 207px;
    font-family: "Arimo", sans-serif;
    font-size: 12.5px;
    line-height: 16px;
    color: var(--ink);
    font-style: normal;
  }
  .phone {
    position: absolute;
    right: 28px;
    top: 218px;
    font-family: "Exo 2", sans-serif;
    font-weight: 700;
    font-size: 19px;
    letter-spacing: 0.8px;
    color: var(--phone-grey);
    white-space: nowrap;
  }

  /* Back */
  .brand-back {
    position: absolute;
    left: 0;
    right: 0;
    top: 56px;
    text-align: center;
    color: var(--paper);
    font-family: "Marcellus", serif;
    font-size: 34px;
    letter-spacing: 3px;
    text-transform: uppercase;
    line-height: 1;
  }
  .brand-back .brand-mark {
    background: var(--paper);
    width: 30px;
    height: 30px;
    margin-bottom: 14px;
  }
  .services {
    position: absolute;
    left: 0;
    right: 0;
    top: 182px;
    text-align: center;
    list-style: none;
    font-family: "Arimo", sans-serif;
    font-size: 12.5px;
    line-height: 16.5px;
    color: var(--paper);
  }
</style>
</head>
<body>
<main class="canvas">
  <section class="card card-front" aria-label="Business card front">
    <div class="name-band">
      <p class="person-name">Dwayne Halster</p>
      <p class="person-role">Owner</p>
    </div>
    <p class="brand-front"><span class="brand-mark"></span>Corvane<br>Construction</p>
    <address class="address">4875 FM 309<br>Dunmore, TX 79412</address>
    <p class="phone">(325) 482-5096</p>
  </section>

  <section class="card card-back" aria-label="Business card back">
    <p class="brand-back"><span class="brand-mark"></span>Corvane</p>
    <ul class="services">
      <li>Roads, Substation Pads | Temporary Pads | Site Pads,</li>
      <li>Land Leveling | Powerline Row Cleaning | Land Clearing</li>
      <li>Gates | Fencing,Construction Entrances | Excavation</li>
      <li>Trenching | Underground Utilities | Directional Boring | Pile Driving.</li>
    </ul>
  </section>
</main>
</body>
</html>
```